Redesign of business card for Cedar Ridge Mechanical

We are looking for a new design for our business cards for Cedar Ridge Mechanical. We are a plumbing & HVAC construction company, operating on the West Coast of Canada and USA. Logo attached.
Industry/Entity Type
Construction - Plumbing & HVAC
Contact Information for Business Card
Name, address, phone numbers, email, website address
Look and feel
Each slider illustrates characteristics of the customer's brand and the style your logo design should communicate.

```html
<!DOCTYPE html>
<html lang="en">
<head>
<meta charset="utf-8">
<title>Cedar Ridge Mechanical – Business Card</title>
<link href="https://fonts.googleapis.com/css2?family=Poppins:wght@300;400;600&display=swap" rel="stylesheet">
<style>
  :root {
    --stage: #232323;
    --card: #1f1f21;
    --ink: #ffffff;
    --ink-soft: #e6e6e6;
    --ghost: #2c2c2f;
  }
  * { box-sizing: border-box; margin: 0; padding: 0; }
  html, body { width: 1200px; height: 780px; overflow: hidden; }
  body {
    background: var(--stage);
    font-family: "Poppins", sans-serif;
    color: var(--ink);
    display: flex;
    align-items: center;
    justify-content: center;
    gap: 60px;
  }
  .card {
    position: relative;
    width: 500px;
    height: 286px;
    background: var(--card);
    border-radius: 4px;
    overflow: hidden;
    box-shadow: 0 18px 40px rgba(0,0,0,.45);
  }
  .brand {
    display: flex;
    align-items: center;
    gap: 10px;
    font-weight: 600;
    color: var(--ink);
    text-transform: uppercase;
    letter-spacing: .04em;
    line-height: 1.15;
  }
  .brand-square { background: var(--ink); flex: none; }

  /* Contact side */
  .card-front .brand { position: absolute; left: 30px; top: 28px; font-size: 16px; }
  .card-front .brand-square { width: 16px; height: 16px; }
  .contact-list {
    position: absolute; left: 30px; top: 96px;
    list-style: none; font-size: 11.5px; font-weight: 300;
    color: var(--ink-soft); line-height: 1.7;
  }
  .contact-list li { display: flex; align-items: center; gap: 8px; }
  .contact-list .address { padding-left: 20px; }
  .contact-list svg { width: 12px; height: 12px; fill: var(--ink); flex: none; }
  .ghost-square {
    position: absolute; right: 36px; bottom: -30px;
    width: 210px; height: 160px;
    background: var(--ghost); border-radius: 14px;
  }
  .person {
    position: absolute; right: 48px; bottom: 34px; text-align: right;
  }
  .person-name { font-size: 26px; line-height: 1.1; }
  .person-name .first { font-weight: 600; }
  .person-name .last { font-weight: 300; }
  .person-title { font-size: 13px; font-weight: 300; margin-top: 4px; }
  .edge-bar {
    position: absolute; right: 0; bottom: 0;
    width: 22px; height: 96px; background: var(--ink);
  }

  /* Logo side */
  .card-back { display: flex; align-items: center; justify-content: center; }
  .card-back .brand { font-size: 24px; }
  .card-back .brand-square { width: 24px; height: 24px; }
</style>
</head>
<body>
  <section class="card card-front" aria-label="Business card, contact side">
    <div class="brand"><span class="brand-square"></span><span>Cedar Ridge<br>Mechanical</span></div>
    <ul class="contact-list">
      <li class="address">418 Harbor Ave. Suite 300</li>
      <li class="address">Tacoma, WA 98402</li>
      <li>
        <svg viewBox="0 0 24 24" aria-hidden="true"><path d="M6.6 10.8a15.1 15.1 0 0 0 6.6 6.6l2.2-2.2a1 1 0 0 1 1-.25 11.4 11.4 0 0 0 3.6.57 1 1 0 0 1 1 1V20a1 1 0 0 1-1 1A17 17 0 0 1 3 4a1 1 0 0 1 1-1h3.5a1 1 0 0 1 1 1c0 1.25.2 2.45.57 3.57a1 1 0 0 1-.25 1z"/></svg>
        (253) 555-0147
      </li>
      <li>
        <svg viewBox="0 0 24 24" aria-hidden="true"><path d="M2 5h20v14H2zm2 2v.5l8 5 8-5V7zm0 2.8V17h16V9.8l-8 5z"/></svg>
        info@cedarridgemech.com
      </li>
      <li>
        <svg viewBox="0 0 24 24" aria-hidden="true"><path d="M12 2a10 10 0 1 0 0 20 10 10 0 0 0 0-20zm6.9 9h-3a15 15 0 0 0-1.3-6 8 8 0 0 1 4.3 6zM12 4.1c.9 1.3 1.7 3.6 1.9 6.9h-3.8c.2-3.3 1-5.6 1.9-6.9zM9.4 5a15 15 0 0 0-1.3 6h-3a8 8 0 0 1 4.3-6zM5.1 13h3a15 15 0 0 0 1.3 6 8 8 0 0 1-4.3-6zm6.9 6.9c-.9-1.3-1.7-3.6-1.9-6.9h3.8c-.2 3.3-1 5.6-1.9 6.9zm2.6-.9a15 15 0 0 0 1.3-6h3a8 8 0 0 1-4.3 6z"/></svg>
        www.cedarridgemech.com
      </li>
    </ul>
    <div class="ghost-square" aria-hidden="true"></div>
    <div class="person">
      <p class="person-name"><span class="first">Marta</span> <span class="last">Lindqvist</span></p>
      <p class="person-title">Founder &amp; CEO</p>
    </div>
    <div class="edge-bar" aria-hidden="true"></div>
  </section>

  <section class="card card-back" aria-label="Business card, brand side">
    <div class="brand"><span class="brand-square"></span><span>Cedar Ridge Mechanical</span></div>
  </section>
</body>
</html>
```